Construction proffessionals servicing the inner suburbs of Melbournes NorthWest specialising in aler

I would like a web site that is sharp, contemporary and simple to navigate, ie.not too many pages. i would like a home page with some info about us, who we are what our history is and my passion for building and construction based on impeccable customer focus. i would like a projects page and somewhere for clients to add testimonials. i would like a project calculator as well so prospective clients can work out a rough budget prior to contacting. i would like the colours to be in line with my logo which i have uploaded. i have many photos which can be used and can be shared via drop box when required. I would like it to be personal to capture our transparent process. i would like to add our company process as well. be brave and take risks.

Target Market(s)

People renovating and extending their homes, people needing inspections on new homes and pre-purchase inspections

Industry/Entity Type

Construction

Number of Pages Required

5+ page

Requirements
Must have
• Professional, easy to navigate, provide viewers with a happy experience, look great, contacts, project calculator, link through to my training company www.qdmn.learnhub.example also check rowenhq on instagram for pics
Nice to have
• Links to instagram, fonts to match email signature

```html
<!DOCTYPE html>
<html lang="en">
<head>
<meta charset="utf-8">
<title>Rowen Construction</title>
<link rel="stylesheet" href="https://fonts.googleapis.com/css2?family=Open+Sans:wght@400;600;700&family=Roboto:wght@400;500;700&display=swap">
<style>
:root{
  --orange:#f5a623;
  --ink:#333;
  --muted:#666;
  --dark:#2b2b2b;
  --grey:#6d6d6d;
  --light:#f4f4f4;
  --white:#fff;
}
*{box-sizing:border-box;margin:0;padding:0}
html,body{width:727px;height:1200px;overflow:hidden}
body{font-family:"Open Sans",Arial,sans-serif;color:var(--ink);background:var(--white);font-size:8px;line-height:1.45}
.site-header{height:68px;position:relative}
.brand{position:absolute;left:50px;top:8px;display:flex;align-items:center;gap:6px}
.brand-mark{width:18px;height:18px;background:var(--orange)}
.brand-name{font-family:"Roboto",sans-serif;font-weight:700;font-size:30px;color:var(--orange);line-height:1}
.header-note{position:absolute;right:50px;top:12px;font-size:8px;color:var(--muted)}
.header-note a{color:var(--orange);text-decoration:none}
.main-nav{position:absolute;right:50px;top:40px;display:flex}
.main-nav a{font-size:9px;color:var(--ink);text-decoration:none;padding:6px 14px}
.main-nav a.active{background:var(--orange);color:var(--white)}
.hero{height:247px;background:linear-gradient(160deg,#c9ccd0 0%,#9aa3ad 45%,#5c6570 100%)}
.tagline{height:30px;background:var(--orange);color:var(--white);text-align:center;font-family:"Roboto",sans-serif;font-size:11px;font-weight:500;line-height:30px;letter-spacing:.3px}
.section-title{font-family:"Roboto",sans-serif;font-size:15px;font-weight:500;text-align:center}
.section-title::after{content:"";display:block;width:30px;height:2px;background:var(--orange);margin:4px auto 0}
.about{height:150px;padding-top:24px;text-align:center}
.about p{width:560px;margin:10px auto 0;color:var(--muted);font-size:7.5px}
.btn{display:inline-block;background:var(--orange);color:var(--white);font-size:8px;padding:4px 12px;border-radius:2px;text-decoration:none}
.about .btn{margin-top:10px}
.projects{height:260px;background:var(--dark);padding-top:16px}
.projects .section-title{color:var(--white)}
.project-grid{display:flex;gap:15px;justify-content:center;margin-top:16px}
.project-card{width:130px;height:178px;background:var(--white);text-align:center}
.project-photo{width:100px;height:100px;border-radius:50%;margin:10px auto 0;background:radial-gradient(circle at 40% 40%,#c9a46a,#7a6650)}
.project-card h3{font-family:"Roboto",sans-serif;font-size:10px;font-weight:500;margin-top:8px;color:var(--ink)}
.project-card p{font-size:7px;color:var(--muted);padding:3px 10px 0}
.cta-band{height:110px;background:var(--light);display:flex;gap:10px;justify-content:center;padding-top:12px}
.cta-box{width:310px;height:86px;padding:10px 16px;color:var(--white);text-align:center;position:relative;font-size:8px}
.cta-box.calc{background:var(--orange)}
.cta-box.method{background:var(--grey)}
.cta-box .btn{background:var(--white);color:var(--ink);font-weight:600;position:absolute;left:50%;transform:translateX(-50%);bottom:10px;white-space:nowrap}
.who{height:120px;display:flex;gap:16px;padding:14px 0 0 53px}
.who-photo{width:121px;height:85px;background:linear-gradient(135deg,#b9bec4,#7d858e)}
.who-text{width:480px}
.who-text h2{font-family:"Roboto",sans-serif;font-size:14px;color:var(--orange);font-weight:500}
.who-text p{font-size:7.5px;color:var(--muted);margin-top:3px}
.who-text ul{list-style:none;margin-top:4px}
.who-text li{font-size:7.5px;color:var(--muted);padding-left:10px;position:relative}
.who-text li::before{content:"";position:absolute;left:0;top:4px;width:4px;height:4px;background:var(--orange)}
.testimonials{height:175px;padding-top:14px}
.quote-row{display:flex;justify-content:center;gap:30px;margin-top:20px}
.quote{width:300px;display:flex;gap:10px}
.quote-photo{width:48px;height:48px;flex:none;background:linear-gradient(135deg,#8e8e8e,#4a4a4a)}
.quote p{font-size:7.5px;color:var(--muted)}
.site-footer{height:40px;background:var(--orange);display:flex;align-items:center;justify-content:space-between;padding:0 50px}
.footer-nav a{color:var(--white);font-size:8px;text-decoration:none;margin-right:18px}
.social{display:flex;gap:5px}
.social span{width:10px;height:10px;background:var(--white);border-radius:2px}
</style>
</head>
<body>
<header class="site-header">
  <div class="brand"><span class="brand-mark"></span><span class="brand-name">ROWEN</span></div>
  <div class="header-note">Please Visit Our Training Company Website <a href="#">www.qdmn.learnhub.example</a></div>
  <nav class="main-nav">
    <a class="active" href="#">Home</a><a href="#">About Us</a><a href="#">Who We are</a><a href="#">Projects</a><a href="#">Testimonials</a><a href="#">Contact Us</a>
  </nav>
</header>

<section class="hero" role="img" aria-label="Photo of two builders in hard hats shaking hands in front of a construction site"></section>
<div class="tagline">PROVIDING QUALITY EXPERT ADVICE, COMMON SENSE AND FRIENDLY PROFESSIONAL SERVICE</div>

<section class="about">
  <h2 class="section-title">About Us</h2>
  <p>We are a family-run building team serving Melbourne's inner north-west. For over twenty years we have renovated, extended and inspected homes with a clear, honest process. Every job is run with care, open pricing and regular updates, so you always know where your project stands and what comes next.</p>
  <a class="btn" href="#">Read More</a>
</section>

<section class="projects">
  <h2 class="section-title">Our Projects</h2>
  <div class="project-grid">
    <article class="project-card"><div class="project-photo" role="img" aria-label="Photo of a builder at work"></div><h3>Lorem Ipsum Dollar Sit</h3><p>Rear extension with open living and new deck area.</p></article>
    <article class="project-card"><div class="project-photo" role="img" aria-label="Photo of workers on a site"></div><h3>Lorem Ipsum Dollar Sit</h3><p>Full kitchen renovation finished on time and on budget.</p></article>
    <article class="project-card"><div class="project-photo" role="img" aria-label="Photo of a brick house"></div><h3>Lorem Ipsum Dollar Sit</h3><p>Pre-purchase inspection with a clear written report.</p></article>
    <article class="project-card"><div class="project-photo" role="img" aria-label="Photo of a renovated home"></div><h3>Lorem Ipsum Dollar Sit</h3><p>Second storey addition for a growing family home.</p></article>
  </div>
</section>

<section class="cta-band">
  <div class="cta-box calc"><p>Planning a renovation? Use our calculator to work out a rough budget before you get in touch with our team.</p><a class="btn" href="#">PROJECT CALCULATOR</a></div>
  <div class="cta-box method"><p>See how we work, step by step, from first visit and quote to final handover of your home.</p><a class="btn" href="#">PROJECT METHODOLOGY</a></div>
</section>

<section class="who">
  <div class="who-photo" role="img" aria-label="Photo of the building team on site"></div>
  <div class="who-text">
    <h2>Who We are</h2>
    <p>Building is my passion. I started as an apprentice carpenter and built this business on honest advice and real care for every client.</p>
    <ul>
      <li>Registered builders with full insurance cover</li>
      <li>Transparent quotes with no hidden costs</li>
      <li>Regular updates from start to handover</li>
    </ul>
  </div>
</section>

<section class="testimonials">
  <h2 class="section-title">Testimonials</h2>
  <div class="quote-row">
    <div class="quote"><div class="quote-photo" role="img" aria-label="Portrait photo of a client"></div><p>The team extended our home with no fuss. They kept us updated every week, stayed on budget and left the site clean. We would happily recommend them to anyone planning a renovation.</p></div>
    <div class="quote"><div class="quote-photo" role="img" aria-label="Portrait photo of a client"></div><p>Our pre-purchase inspection was thorough and easy to follow. The report explained every issue clearly and helped us negotiate a fair price on our first home.</p></div>
  </div>
</section>

<footer class="site-footer">
  <nav class="footer-nav"><a href="#">Home</a><a href="#">About Us</a><a href="#">Who We are</a><a href="#">Projects</a><a href="#">Testimonials</a><a href="#">Contact Us</a></nav>
  <div class="social"><span></span><span></span><span></span><span></span></div>
</footer>
</body>
</html>
```